Brookvale Estates LLC stationary for a real estate property management company.

Create stationary (letterhead, envelopes, business cards) using Brookvale Estates LLC logo as primary creative element. Stationary design needs to be horizontal, leaving as much space as possible for correspondence copy. See attached Creative Brief and past stationary files for details.

Target Market(s)

Prospective apartment residents and current residents, vendors, and government agencies.

Industry/Entity Type

Property Management

Contact Information for Business Card

Business card employee title: Property Manager. Should include address, phone, fax, email, website, slogan, and Brookvale Estates logo.

Font styles to use
Sans Serif

Colors
0592cd
000000

Requirements
Must have
• Tone should be conservative, institutional, business (i.e. banking, finance, real estate). Must include: address, phone, fax, website, and slogan (see attached Creative Brief). Should be a horizontal design, leaving as much room as possible for letter correspondence copy.
Nice to have
• Please use an Arial or Helvetica style font.
Should not have
• Letterhead layout should leave as much room as possible for copy.

```html
<!DOCTYPE html>
<html lang="en">
<head>
<meta charset="utf-8">
<title>Brookvale Estates LLC – Business Card</title>
<link href="https://fonts.googleapis.com/css2?family=Roboto:wght@400;500;700&display=swap" rel="stylesheet">
<style>
  :root {
    --brand-blue: #0a6fae;
    --brand-blue-light: #17b4e8;
    --brand-blue-dark: #0b5f9c;
    --ink-grey: #4a4a4c;
    --text-grey: #555;
    --card-white: #f7f7f7;
    --backdrop: #e6e6e6;
  }
  * { margin: 0; padding: 0; box-sizing: border-box; }
  html, body { width: 1200px; height: 960px; overflow: hidden; }
  body {
    background: var(--backdrop);
    font-family: "Roboto", Arial, Helvetica, sans-serif;
    position: relative;
  }
  .card {
    position: absolute;
    width: 600px;
    height: 342px;
    box-shadow: 0 3px 8px rgba(0,0,0,0.25);
    overflow: hidden;
  }
  .card--front { left: 302px; top: 129px; background: var(--card-white); }
  .card--back {
    left: 299px; top: 488px;
    background: linear-gradient(135deg, var(--brand-blue-light) 0%, var(--brand-blue) 45%, var(--brand-blue-dark) 100%);
  }
  .brand-panel {
    position: absolute; left: 0; top: 0;
    width: 190px; height: 100%;
    background: linear-gradient(160deg, var(--ink-grey) 0%, #3f6e94 45%, var(--brand-blue) 100%);
  }
  .front-details {
    position: absolute; right: 32px; top: 0;
    text-align: right;
    color: var(--text-grey);
    font-size: 14px;
  }
  .wordmark {
    display: flex; align-items: center; justify-content: flex-end;
    gap: 10px;
    margin-top: 60px;
    color: var(--brand-blue);
    font-weight: 700;
    font-size: 25px;
    letter-spacing: 0.5px;
    text-transform: uppercase;
  }
  .wordmark__dot {
    width: 16px; height: 16px; border-radius: 50%;
    background: var(--brand-blue);
  }
  .person-name {
    margin-top: 28px;
    color: var(--brand-blue);
    font-weight: 500;
    font-size: 20px;
    text-transform: uppercase;
  }
  .person-title { font-size: 15px; margin-top: 2px; }
  .address { margin-top: 10px; line-height: 18px; }
  .contact { margin-top: 8px; line-height: 19px; }
  .slogan {
    margin-top: 8px;
    color: var(--brand-blue);
    font-weight: 700;
    font-size: 14px;
  }
  .back-wordmark {
    position: absolute; left: 0; right: 0; top: 148px;
    display: flex; align-items: center; justify-content: center;
    gap: 14px;
    color: #fff;
    font-weight: 700;
    font-size: 38px;
    letter-spacing: 1px;
    text-transform: uppercase;
  }
  .back-wordmark__dot {
    width: 24px; height: 24px; border-radius: 50%;
    background: #fff;
  }
</style>
</head>
<body>
  <section class="card card--front">
    <div class="brand-panel" role="img" aria-label="Decorative brand panel in grey and blue"></div>
    <div class="front-details">
      <div class="wordmark"><span class="wordmark__dot"></span>Brookvale Estates LLC</div>
      <p class="person-name">Dana Whitfield</p>
      <p class="person-title">Property Manager</p>
      <p class="address">2750 Larkspur Avenue #B210<br>Cedar Falls, CA 92018</p>
      <p class="contact">Phone: 555-214-7730<br>Fax: 555-214-7731<br>dana@brookvaleestates.us<br>www.brookvaleestates.us</p>
      <p class="slogan">Multifamily Property Management</p>
    </div>
  </section>

  <section class="card card--back">
    <div class="back-wordmark"><span class="back-wordmark__dot"></span>Brookvale Estates LLC</div>
  </section>
</body>
</html>
```